Single Page Corporate Profile Web-site Design

We're a new IT Resourcing company called vantyx, and we need a ew single page corporate web-site to establish our credentials.

Our model is to extend IT resourcing to offer access to global resources, end to end management, and a structured approach resourcing process.

Phase 2 (out of scope) will be a full site build in approximately a month's time.

This project is to:
- Establish a look and feel for web, consistent with existing design work (logo an corporate presentation)
- Build the web pages
- Upload onto our domain hosting site (K&Q)

The web-site:
We want a modern, clean and bold design.

We'd like a design that is consistent with our corporate presentation (sourceless supplied). In terms of look and feel and use of graphics.

KEY FEATURES
- Single page design.
- Navigation bar (to page sections) at the top of the page.
- No cookies (phase 1 design)
- Good example of preferred web page design:
www.plomvex42.com
https://brisq.com/dial/days-with-brisq-dial/
http://www.talwickmachines.com
- Clear sections on page as structured in the attached slides.
- We would like some of the page sections to use imagery of your choice - but please no cliched "IT people" or "data-centre" images.
- Image use must be royalty free.

ANY ADVICE WELCOME ! It's been a while since we've done this.

Target Market(s)

Companies - mid-size, technically sophisticated IT developers.
Potential employees

Industry/Entity Type

It Company

Number of Pages Required

1 page

Font styles to use
Other font styles liked:
• calibri

Requirements
Must have
• Do's
• - Please use graphics and "look and feel" provided
• - Follow similar style of those sites provided
• - Take the provided content and develop it for the web
• - Page must load quickly (if you think there's too much on the page - say so, and we'll put it across a few"
• - Please use background imagery for some of the sections
Should not have
• Don'ts
• - Please don't use cliched imagery e.g. "IT people" or "data-centre lights"
• - Use dark colours

```html
<!DOCTYPE html>
<html lang="en">
<head>
<meta charset="utf-8">
<title>vantyx – IT Resourcing</title>
<link rel="stylesheet" href="https://fonts.googleapis.com/css2?family=Open+Sans:wght@400;600;700;800&display=swap">
<style>
:root{
  --navy:#1d3486;
  --navy-dark:#172a6c;
  --orange:#f26a1b;
  --orange-mid:#f49a4a;
  --orange-light:#f8b97a;
  --orange-pale:#fbd3a8;
  --ink:#2b2b2b;
  --muted:#666;
  --paper:#ffffff;
  --fog:#f1f1f1;
  --line:#d9d9d9;
  --sky:#3a93dd;
}
*{box-sizing:border-box;margin:0;padding:0}
html,body{width:1200px;height:4286px;overflow:hidden}
body{font-family:"Open Sans",Arial,sans-serif;color:var(--ink);background:var(--paper);position:relative}
.abs{position:absolute}
section,header,footer{position:absolute;left:0;width:1200px}
.center{left:0;width:1200px;text-align:center}
.section-title{font-size:22px;font-weight:700;letter-spacing:.5px;color:#111}
.section-sub{font-size:15px;color:#444}

/* header */
.site-header{top:0;height:94px;background:#fff}
.brand{font-weight:700;font-size:40px;color:var(--navy);letter-spacing:-1px;white-space:nowrap}
.nav{top:34px;left:557px;display:flex;gap:0}
.nav a{display:block;font-size:14px;color:#333;text-decoration:none;padding:5px 14px;height:29px;margin-right:10px}
.nav a.active{background:var(--navy);color:#fff}

/* hero */
.hero{top:94px;height:549px;background:linear-gradient(180deg,#eef0f0 0%,#d7dbdc 45%,#aeb3b4 75%,#7e8486 100%);overflow:hidden}
.hero-photo{left:560px;top:0;width:460px;height:549px;background:linear-gradient(180deg,#5a6068 0%,#2f3540 60%,#1f2530 100%);opacity:.55;border-radius:180px 180px 0 0}
.hero h1{left:114px;top:160px;width:420px;font-size:30px;line-height:38px;font-weight:700;color:#111}
.hero-rule{left:114px;top:246px;width:343px;height:2px;background:#333}
.hero-points{left:114px;top:270px;list-style:none}
.hero-points li{display:flex;align-items:center;gap:14px;font-size:16px;font-weight:600;height:36px}
.arrow-btn{top:338px;width:46px;height:46px;border-radius:50%;background:rgba(90,90,90,.55);display:flex;align-items:center;justify-content:center}

/* about */
.about{top:643px;height:265px;background:var(--fog)}
.about p{left:114px;top:94px;width:972px;font-size:12px;line-height:17px;text-align:center;color:#444}
.btn{display:flex;align-items:center;justify-content:center;font-size:11px;font-weight:700;color:#fff;height:26px;width:94px}
.btn-navy{background:var(--navy)}
.btn-orange{background:var(--orange)}

/* iteration */
.iteration{top:908px;height:449px;background:#fff}
.step-line{top:248px;left:326px;width:531px;height:2px;background:var(--navy)}
.step{width:230px;text-align:center}
.step .dot{width:86px;height:86px;border-radius:50%;background:var(--navy);margin:0 auto;display:flex;align-items:center;justify-content:center}
.step h3{margin-top:20px;font-size:14px;font-weight:400}
.step h3 b{font-weight:700}
.step p{margin-top:10px;font-size:12px;line-height:17px;color:#555}

/* services */
.services{top:1357px;height:414px;background:linear-gradient(90deg,#ece4df 0%,#f3ece8 40%,#ead8d0 75%,#dcc2b8 100%)}
.tab{top:114px;height:58px;display:flex;align-items:center;justify-content:center;font-size:18px;font-weight:700;color:#fff;letter-spacing:.5px}
.tab-on{left:277px;width:252px;background:var(--orange)}
.tab-off{left:537px;width:392px;background:#c9c9c9}
.svc-div{left:531px;top:232px;width:1px;height:154px;background:#999}
.svc-icon{width:77px;height:54px;background:#555;border-radius:14px 20px 10px 24px;opacity:.8}
.svc-globe{width:54px;height:54px;border-radius:50%;background:#5d5d5d}
.svc h3{font-size:16px;font-weight:700}
.svc .lead{font-size:13px;font-weight:700;color:#333;margin-top:8px}
.svc ul{list-style:none;margin-top:8px}
.svc li{font-size:13px;color:#333;display:flex;gap:10px;align-items:center;height:27px}

/* DNA */
.dna{top:1771px;height:558px;background:#fff}
.dna-copy{left:97px;top:145px;width:340px;font-size:14px;line-height:21px;color:#333}
.dna-copy p{margin-bottom:15px}
.grid{left:471px;top:189px;width:629px}
.g-head-res{position:absolute;left:0;top:-83px;width:306px;height:80px;background:var(--orange);text-align:center;color:#fff}
.g-head-res b{display:block;font-size:30px;font-weight:700;letter-spacing:1px;padding-top:6px}
.g-head-res span{display:block;font-size:12px;font-weight:700}
.g-head{position:absolute;top:-83px;height:80px;text-align:center;color:#222;background:#fff;border:1px solid var(--line)}
.g-head b{display:block;font-size:24px;font-weight:600;padding-top:10px;line-height:24px}
.g-head span{font-size:11px;color:#555}
.g-row{display:flex;height:25.5px}
.g-row .lbl{width:306px;font-size:11px;font-weight:600;color:#222;padding-left:10px;display:flex;align-items:center}
.g-row .c{display:flex;align-items:center;justify-content:center}
.g-row .gold{width:152px}
.g-row .gap{width:8px}
.g-row .plat{width:163px}
.g-row:nth-child(odd) .lbl,.g-row:nth-child(odd) .gold{background:var(--orange-light)}
.g-row:nth-child(even) .lbl,.g-row:nth-child(even) .gold{background:var(--orange-pale)}
.g-row:nth-child(odd) .plat{background:var(--orange-mid)}
.g-row:nth-child(even) .plat{background:var(--orange-light)}

/* technology */
.tech{top:2329px;height:485px;background:var(--navy);color:#fff}
.tech .section-title,.tech .section-sub{color:#fff}
.tech-col{width:320px}
.tech-col .ic{width:86px;height:86px;border-radius:50%;background:var(--sky);margin:0 auto 0 107px;display:flex;align-items:center;justify-content:center}
.tech-col h3{text-align:center;width:300px;font-size:17px;font-weight:600;line-height:29px;margin-top:10px}
.tech-col .roles{text-align:center;width:300px;font-size:13px;margin-top:8px}
.tech-col ul{list-style:none;margin:20px 0 0 40px}
.tech-col li{font-size:12px;line-height:16px;min-height:32px;display:flex;gap:10px;align-items:flex-start;padding-top:2px}
.tech-col li svg{flex:none;margin-top:2px}
.tech-div{top:88px;width:1px;height:271px;background:rgba(255,255,255,.3)}

/* delivery */
.delivery{top:2814px;height:929px;background:#fff}
.timeline{left:619px;top:237px;width:0;height:635px;border-left:2px dotted var(--orange)}
.tl-num{font-size:15px;font-weight:600;color:var(--orange)}
.card{width:366px;background:#fff;border:1px solid #ddd;box-shadow:0 2px 6px rgba(0,0,0,.08);padding:26px 20px 20px 104px}
.card .ic{position:absolute;left:30px;top:26px;width:50px;height:50px;border:1px solid #ddd;display:flex;align-items:center;justify-content:center}
.card h3{font-size:13px;font-weight:700;color:var(--navy)}
.card p{font-size:12px;line-height:17px;color:#555;margin-top:8px}

/* contact */
.contact{top:3743px;height:480px;background:#fff}
.ct-label{font-size:13px;letter-spacing:2px;color:#333}
.ct-val{font-size:13px;color:#333;line-height:23px}
.form{left:434px;top:177px;width:572px;height:237px;background:var(--fog)}
.field{background:#fff;font-size:10px;color:#999;padding:10px 12px;letter-spacing:1px}
.send{background:var(--orange);color:#fff;font-size:12px;font-weight:700;display:flex;align-items:center;justify-content:center;letter-spacing:1px}
.ct-caption{left:434px;top:440px;font-size:10px;color:#888;letter-spacing:1px}

/* footer */
.site-footer{top:4223px;height:63px;background:var(--navy);color:#fff}
.site-footer .brand{color:#fff;font-size:24px;top:15px;left:97px}
.copy{left:186px;top:24px;font-size:11px}
.social{top:17px;width:28px;height:28px;border-radius:50%;background:#fff}
</style>
</head>
<body>

<header class="site-header">
  <div class="abs brand" style="left:97px;top:18px">vantyx</div>
  <nav class="abs nav">
    <a class="active" href="#about">About Us</a>
    <a href="#services">Services</a>
    <a href="#dna">Our DNA</a>
    <a href="#tech">Competencies</a>
    <a href="#delivery">Delivery</a>
    <a href="#contact">Contact</a>
  </nav>
</header>

<section class="hero">
  <div class="abs hero-photo" role="img" aria-label="Business man opening his shirt to reveal a branded t-shirt in front of a city skyline"></div>
  <h1 class="abs">We wanted to do something different</h1>
  <div class="abs hero-rule"></div>
  <ul class="abs hero-points">
    <li><svg width="20" height="20" viewBox="0 0 20 20"><circle cx="10" cy="10" r="9" fill="none" stroke="#222" stroke-width="1.6"/><path d="M8 6l4 4-4 4" fill="none" stroke="#222" stroke-width="1.6"/></svg>Charge less, for doing more.</li>
    <li><svg width="20" height="20" viewBox="0 0 20 20"><circle cx="10" cy="10" r="9" fill="none" stroke="#222" stroke-width="1.6"/><path d="M8 6l4 4-4 4" fill="none" stroke="#222" stroke-width="1.6"/></svg>Always deliver.</li>
    <li><svg width="20" height="20" viewBox="0 0 20 20"><circle cx="10" cy="10" r="9" fill="none" stroke="#222" stroke-width="1.6"/><path d="M8 6l4 4-4 4" fill="none" stroke="#222" stroke-width="1.6"/></svg>Bring some rigour.</li>
  </ul>
  <div class="abs arrow-btn" style="left:28px"><svg width="16" height="16" viewBox="0 0 16 16"><path d="M10 3L5 8l5 5" fill="none" stroke="#fff" stroke-width="2"/></svg></div>
  <div class="abs arrow-btn" style="left:1123px"><svg width="16" height="16" viewBox="0 0 16 16"><path d="M6 3l5 5-5 5" fill="none" stroke="#fff" stroke-width="2"/></svg></div>
</section>

<section class="about" id="about">
  <h2 class="abs center section-title" style="top:46px">ABOUT US</h2>
  <p class="abs">We created vantyx because we wanted to offer something different in IT resourcing. We're expert at what we do with a track record of IT Service Delivery and Resourcing excellence in high growth environments.Reid Halvorsen – With a background in sales management and recruitment, Reid founded a highly successful recruitment agency and built it into one of the UK's leading specialist agencies. Successfully exiting the business after 10 years.Milo Tennant – With a history in telecoms and IT services, Milo has held many senior level positions from marketing to operations. His last role was as COO for an IT services company supporting the growth from 250 to 2000 people whilst he was there.One of our core aims with vantyx is to build a fantastic team. Happy team, happy customers, successful business !</p>
  <div class="abs btn btn-navy" style="left:500px;top:203px">READ MORE</div>
  <div class="abs btn btn-orange" style="left:606px;top:203px">VIEW WORKS</div>
</section>

<section class="iteration">
  <h2 class="abs center section-title" style="top:32px">AN ITERATION OF TRADITIONAL RESOURCING</h2>
  <p class="abs center section-sub" style="top:60px">In a market where outstanding people are hard to find, we wanted to offer a solution:</p>
  <div class="abs center brand" style="top:100px;font-size:46px">vantyx</div>
  <div class="abs step-line"></div>
  <div class="abs step" style="left:211px;top:206px">
    <div class="dot"><svg width="34" height="34" viewBox="0 0 34 34"><circle cx="17" cy="17" r="12" fill="none" stroke="#fff" stroke-width="3"/><path d="M17 10v7l5 3" fill="none" stroke="#fff" stroke-width="3"/></svg></div>
    <h3><b>TIME</b> TO HIRE</h3>
    <p>Combine local market coverage, with access to global markets to deliver exceptional people quickly.</p>
  </div>
  <div class="abs step" style="left:471px;top:206px">
    <div class="dot"><svg width="36" height="30" viewBox="0 0 36 30"><rect x="3" y="5" width="30" height="20" fill="none" stroke="#fff" stroke-width="3"/><circle cx="18" cy="15" r="5" fill="none" stroke="#fff" stroke-width="3"/></svg></div>
    <h3><b>COST</b> TO HIRE</h3>
    <p>Combine local market coverage, with access to global markets to deliver exceptional people quickly.</p>
  </div>
  <div class="abs step" style="left:742px;top:206px">
    <div class="dot"><svg width="34" height="34" viewBox="0 0 34 34"><path d="M7 17l7 7 13-14" fill="none" stroke="#fff" stroke-width="4"/></svg></div>
    <h3><b>QUALITY</b> OF HIRES</h3>
    <p>Combine local market coverage, with access to global markets to deliver exceptional people quickly.</p>
  </div>
</section>

<section class="services" id="services" role="img" aria-label="Soft warm background photograph behind the services section">
  <h2 class="abs center section-title" style="top:24px">OUR SERVICES</h2>
  <p class="abs center section-sub" style="top:52px">Our focus is on saving you time and money on your IT resourcing, without compromising quality</p>
  <div class="abs tab tab-on">vantyx RESOURCING</div>
  <div class="abs tab tab-off">vantyx RESOURCING MANAGEMENT</div>
  <div class="abs svc-div"></div>
  <div class="abs svc-icon" style="left:94px;top:232px" role="img" aria-label="Map of the United Kingdom"></div>
  <div class="abs svc" style="left:191px;top:234px">
    <h3>LOCAL</h3>
    <div class="lead">High quality IT resources delivered on-site</div>
    <ul><li><svg width="14" height="14" viewBox="0 0 14 14"><circle cx="7" cy="7" r="6" fill="none" stroke="#333"/><path d="M6 4l3 3-3 3" fill="none" stroke="#333"/></svg>Permanent or contract hires</li></ul>
  </div>
  <div class="abs svc-globe" style="left:560px;top:232px" role="img" aria-label="Globe"></div>
  <div class="abs svc" style="left:631px;top:234px">
    <h3>GLOBAL</h3>
    <div class="lead">Access to global markets to deliver hard to find resources</div>
    <ul>
      <li><svg width="14" height="14" viewBox="0 0 14 14"><circle cx="7" cy="7" r="6" fill="none" stroke="#333"/><path d="M6 4l3 3-3 3" fill="none" stroke="#333"/></svg>High quality IT resourcing delivered from Eastern Europe.</li>
      <li><svg width="14" height="14" viewBox="0 0 14 14"><circle cx="7" cy="7" r="6" fill="none" stroke="#333"/><path d="M6 4l3 3-3 3" fill="none" stroke="#333"/></svg>Near-shoring – Permanent, flexible and project delivery solutions.</li>
      <li><svg width="14" height="14" viewBox="0 0 14 14"><circle cx="7" cy="7" r="6" fill="none" stroke="#333"/><path d="M6 4l3 3-3 3" fill="none" stroke="#333"/></svg>On-shoring – Bringing global resources to the UK.</li>
    </ul>
  </div>
</section>

<section class="dna" id="dna">
  <h2 class="abs center section-title" style="top:44px">OUR DNA</h2>
  <div class="abs dna-copy">
    <p>vantyx RESOURCE is our best practice resourcing toolset. Included every time.</p>
    <p>Defined, proven, measurable processes.</p>
    <p>Assuring resource quality, time and cost.</p>
  </div>
  <div class="abs btn btn-navy" style="left:97px;top:303px;width:132px;height:29px">KNOW MORE</div>
  <div class="abs grid">
    <div class="g-head-res"><b>RESOURCE</b><span>YOUR BEST PRACTICE TOOLSET</span></div>
    <div class="g-head" style="left:306px;width:152px"><b>GOLD</b><span>STANDARD</span></div>
    <div class="g-head" style="left:466px;width:163px;top:-91px;height:88px"><b>PLATINUM</b><span>OPTIONS</span></div>
    <div class="g-row"><div class="lbl">Workforce Planning</div><div class="c gold"></div><div class="gap"></div><div class="c plat"><svg width="16" height="14"><path d="M2 7l4 4 8-9" fill="none" stroke="#fff" stroke-width="3"/></svg></div></div>
    <div class="g-row"><div class="lbl">Process audit and design</div><div class="c gold"></div><div class="gap"></div><div class="c plat"><svg width="16" height="14"><path d="M2 7l4 4 8-9" fill="none" stroke="#fff" stroke-width="3"/></svg></div></div>
    <div class="g-row"><div class="lbl">Candidate experience mapping</div><div class="c gold"></div><div class="gap"></div><div class="c plat"><svg width="16" height="14"><path d="M2 7l4 4 8-9" fill="none" stroke="#fff" stroke-width="3"/></svg></div></div>
    <div class="g-row"><div class="lbl">Candidate Specification &amp; Profiling</div><div class="c gold"><svg width="16" height="14"><path d="M2 7l4 4 8-9" fill="none" stroke="#fff" stroke-width="3"/></svg></div><div class="gap"></div><div class="c plat"><svg width="16" height="14"><path d="M2 7l4 4 8-9" fill="none" stroke="#fff" stroke-width="3"/></svg></div></div>
    <div class="g-row"><div class="lbl">Candidate Attraction</div><div class="c gold"><svg width="16" height="14"><path d="M2 7l4 4 8-9" fill="none" stroke="#fff" stroke-width="3"/></svg></div><div class="gap"></div><div class="c plat"><svg width="16" height="14"><path d="M2 7l4 4 8-9" fill="none" stroke="#fff" stroke-width="3"/></svg></div></div>
    <div class="g-row"><div class="lbl">Candidate Relationship Management</div><div class="c gold"><svg width="16" height="14"><path d="M2 7l4 4 8-9" fill="none" stroke="#fff" stroke-width="3"/></svg></div><div class="gap"></div><div class="c plat"><svg width="16" height="14"><path d="M2 7l4 4 8-9" fill="none" stroke="#fff" stroke-width="3"/></svg></div></div>
    <div class="g-row"><div class="lbl">Screening, Selection &amp; Vetting</div><div class="c gold"><svg width="16" height="14"><path d="M2 7l4 4 8-9" fill="none" stroke="#fff" stroke-width="3"/></svg></div><div class="gap"></div><div class="c plat"><svg width="16" height="14"><path d="M2 7l4 4 8-9" fill="none" stroke="#fff" stroke-width="3"/></svg></div></div>
    <div class="g-row"><div class="lbl">Technical and behavioral evaluation</div><div class="c gold"><svg width="16" height="14"><path d="M2 7l4 4 8-9" fill="none" stroke="#fff" stroke-width="3"/></svg></div><div class="gap"></div><div class="c plat"><svg width="16" height="14"><path d="M2 7l4 4 8-9" fill="none" stroke="#fff" stroke-width="3"/></svg></div></div>
    <div class="g-row"><div class="lbl">Hiring &amp; Onboarding</div><div class="c gold"></div><div class="gap"></div><div class="c plat"><svg width="16" height="14"><path d="M2 7l4 4 8-9" fill="none" stroke="#fff" stroke-width="3"/></svg></div></div>
    <div class="g-row"><div class="lbl">On-shoring of global resources to UK</div><div class="c gold"></div><div class="gap"></div><div class="c plat"><svg width="16" height="14"><path d="M2 7l4 4 8-9" fill="none" stroke="#fff" stroke-width="3"/></svg></div></div>
    <div class="g-row"><div class="lbl">Supply Chain Management</div><div class="c gold"></div><div class="gap"></div><div class="c plat"><svg width="16" height="14"><path d="M2 7l4 4 8-9" fill="none" stroke="#fff" stroke-width="3"/></svg></div></div>
    <div class="g-row"><div class="lbl">vantyx Service Levels &amp; Penalties</div><div class="c gold"><svg width="16" height="14"><path d="M2 7l4 4 8-9" fill="none" stroke="#fff" stroke-width="3"/></svg></div><div class="gap"></div><div class="c plat"><svg width="16" height="14"><path d="M2 7l4 4 8-9" fill="none" stroke="#fff" stroke-width="3"/></svg></div></div>
    <div class="g-row"><div class="lbl">Performance Monitoring &amp; Reporting</div><div class="c gold"><svg width="16" height="14"><path d="M2 7l4 4 8-9" fill="none" stroke="#fff" stroke-width="3"/></svg></div><div class="gap"></div><div class="c plat"><svg width="16" height="14"><path d="M2 7l4 4 8-9" fill="none" stroke="#fff" stroke-width="3"/></svg></div></div>
  </div>
</section>

<section class="tech" id="tech">
  <h2 class="abs center section-title" style="top:32px">TECHNOLOGY COMPETENCE</h2>
  <p class="abs center section-sub" style="top:64px;left:200px;width:800px;font-size:14px">We have proven experience in hiring IT resourcing both as a resourcing partner, and in complex global enterprise operational environments.</p>
  <div class="abs tech-div" style="left:434px;top:200px"></div>
  <div class="abs tech-div" style="left:751px;top:200px"></div>
  <div class="abs tech-col" style="left:87px;top:154px">
    <div class="ic"><svg width="40" height="40" viewBox="0 0 40 40"><rect x="6" y="8" width="28" height="20" fill="none" stroke="#fff" stroke-width="3"/><path d="M14 34h12M20 28v6" stroke="#fff" stroke-width="3"/></svg></div>
    <h3>Software<br>Development</h3>
    <div class="roles">Roles across entire SDLC</div>
    <ul>
      <li><svg width="12" height="12"><circle cx="6" cy="6" r="5" fill="none" stroke="#fff"/></svg>Desktop, web &amp; enterprise solutions</li>
      <li><svg width="12" height="12"><circle cx="6" cy="6" r="5" fill="none" stroke="#fff"/></svg>Compiled &amp; managed languages</li>
      <li><svg width="12" height="12"><circle cx="6" cy="6" r="5" fill="none" stroke="#fff"/></svg>Scripting &amp; dynamic languages</li>
    </ul>
  </div>
  <div class="abs tech-col" style="left:450px;top:154px">
    <div class="ic"><svg width="40" height="40" viewBox="0 0 40 40"><rect x="12" y="4" width="16" height="32" rx="3" fill="none" stroke="#fff" stroke-width="3"/><circle cx="20" cy="31" r="1.5" fill="#fff"/></svg></div>
    <h3>Mobile<br>Applications</h3>
    <div class="roles">Roles across entire SDLC</div>
    <ul>
      <li><svg width="12" height="12"><circle cx="6" cy="6" r="5" fill="none" stroke="#fff"/></svg>Native handset platforms</li>
      <li><svg width="12" height="12"><circle cx="6" cy="6" r="5" fill="none" stroke="#fff"/></svg>Tablet applications</li>
      <li><svg width="12" height="12"><circle cx="6" cy="6" r="5" fill="none" stroke="#fff"/></svg>Cross-platform frameworks</li>
    </ul>
  </div>
  <div class="abs tech-col" style="left:764px;top:154px">
    <div class="ic"><svg width="44" height="40" viewBox="0 0 44 40"><circle cx="22" cy="13" r="6" fill="#fff"/><circle cx="10" cy="17" r="4.5" fill="#fff"/><circle cx="34" cy="17" r="4.5" fill="#fff"/><path d="M12 34c0-8 20-8 20 0zM2 33c0-6 12-7 12-3M42 33c0-6-12-7-12-3" fill="#fff"/></svg></div>
    <h3>Senior<br>Appointments</h3>
    <div class="roles">Roles across entire SDLC</div>
    <ul>
      <li><svg width="12" height="12"><circle cx="6" cy="6" r="5" fill="none" stroke="#fff"/></svg>CTO &amp; Development Directors</li>
      <li><svg width="12" height="12"><circle cx="6" cy="6" r="5" fill="none" stroke="#fff"/></svg>Development, Project &amp; Product Managers</li>
      <li><svg width="12" height="12"><circle cx="6" cy="6" r="5" fill="none" stroke="#fff"/></svg>Programme, Service Delivery Management / Directorship</li>
    </ul>
  </div>
</section>

<section class="delivery" id="delivery">
  <h2 class="abs center section-title" style="top:92px">OUR DELIVERY</h2>
  <p class="abs center section-sub" style="top:134px;line-height:29px">If you were delivering a customer IT project you'd do it like this.<br>Why would you not get your resourcing services delivered the same way ?</p>
  <div class="abs timeline"></div>
  <div class="abs tl-num" style="left:650px;top:281px">1</div>
  <div class="abs tl-num" style="left:650px;top:492px">2</div>
  <div class="abs tl-num" style="left:650px;top:632px">3</div>
  <div class="abs tl-num" style="left:600px;top:812px">4</div>
  <div class="abs card" style="left:200px;top:232px;height:120px">
    <div class="ic"><svg width="22" height="26"><path d="M3 2h12l5 5v17H3z" fill="none" stroke="#1d3486" stroke-width="2"/><path d="M7 12h9M7 16h9M7 20h6" stroke="#1d3486" stroke-width="2"/></svg></div>
    <h3>YOUR REQUIREMENTS<br>DEFINED</h3>
    <p>Define and agree your requirements in a Statement of Work</p>
  </div>
  <div class="abs card" style="left:737px;top:386px;height:143px">
    <div class="ic"><svg width="24" height="22"><path d="M2 20c2-8 8-12 14-12V3l7 7-7 7v-5c-6 0-10 2-14 8z" fill="#1d3486"/></svg></div>
    <h3>KICK-OFF</h3>
    <p>We review the project and set it up to ensure success.</p>
  </div>
  <div class="abs card" style="left:200px;top:577px;height:129px">
    <div class="ic"><svg width="24" height="22"><path d="M1 3h4l3 12h12l2-9H7" fill="none" stroke="#1d3486" stroke-width="2"/><circle cx="10" cy="19" r="2" fill="#1d3486"/><circle cx="18" cy="19" r="2" fill="#1d3486"/></svg></div>
    <h3>DELIVERY</h3>
    <p>We deliver your services:<br>vantyx Resourcing, vantyx Resourcing Management.</p>
  </div>
  <div class="abs card" style="left:737px;top:757px;height:132px">
    <div class="ic"><svg width="24" height="24" viewBox="0 0 24 24"><circle cx="12" cy="12" r="4" fill="none" stroke="#1d3486" stroke-width="3"/><path d="M12 2v4M12 18v4M2 12h4M18 12h4M5 5l3 3M16 16l3 3M5 19l3-3M16 8l3-3" stroke="#1d3486" stroke-width="3"/></svg></div>
    <h3>SERVICE MANAGEMENT</h3>
    <p>Offering full transparency and control over your service.</p>
  </div>
</section>

<section class="contact" id="contact">
  <h2 class="abs center section-title" style="top:58px">GET IN TOUCH</h2>
  <p class="abs center section-sub" style="top:96px;font-size:14px">If you think we can help, we'd love to hear from you.</p>
  <div class="abs ct-label" style="left:177px;top:204px">CALL ME</div>
  <div class="abs ct-val" style="left:177px;top:225px">(925) 555-0148</div>
  <div class="abs ct-label" style="left:177px;top:270px">EMAIL ME</div>
  <div class="abs ct-val" style="left:177px;top:292px">hello@vantyx-mail.com</div>
  <div class="abs ct-label" style="left:177px;top:344px">ADDRESS</div>
  <div class="abs ct-val" style="left:177px;top:365px">412 Marlow Ridge Road<br>Fenwick, CA 90210</div>
  <div class="abs form">
    <div class="abs field" style="left:32px;top:49px;width:223px;height:34px">NAME</div>
    <div class="abs field" style="left:32px;top:106px;width:223px;height:34px">EMAIL</div>
    <div class="abs field" style="left:32px;top:154px;width:223px;height:35px">SUBJECT</div>
    <div class="abs field" style="left:286px;top:49px;width:260px;height:91px">TEXTE</div>
    <div class="abs send" style="left:286px;top:154px;width:260px;height:35px">SEND NOW</div>
  </div>
  <div class="abs ct-caption">LOOKING FORWARD TO HEARING FROM YOU</div>
</section>

<footer class="site-footer">
  <div class="abs brand">vantyx</div>
  <div class="abs copy">Copyrights © 2015 vantyx All rights reserved</div>
  <div class="abs social" style="left:980px"></div>
  <div class="abs social" style="left:1014px"></div>
  <div class="abs social" style="left:1048px"></div>
  <div class="abs social" style="left:1082px"></div>
</footer>

</body>
</html>
```